Looking for a cool & simple business-card-design for digital agency

Hi!

We are a web agency that offers Reputation Management, Vextor & Seo Services and software development. We like cool things, we like innovative styles.

We have uploaded our logo.

Project Deadline Extended Reason: Client does not want any designs with the colorful logo. Please send us submissions ONLY with the blac and white logo. What the client would like to see:1) Back of the card: is a silver logo on a black background2) front of the card with all the data, please use white background and black logo thank you Added Friday, May 8, 2015

Industry/Entity Type

Software

```html
<!DOCTYPE html>
<html lang="en">
<head>
<meta charset="utf-8">
<title>Kernwerk AG – Business Card</title>
<link rel="stylesheet" href="https://fonts.googleapis.com/css2?family=Lato:wght@400;700;900&display=swap">
<style>
  :root {
    --stage: #3b3229;
    --card-black: #0a0a0a;
    --card-white: #ffffff;
    --ink: #1a1a1a;
    --silver: #b9b9b9;
    --silver-faint: #181818;
    --tagline: #f2f2f2;
  }
  * { box-sizing: border-box; margin: 0; padding: 0; }
  html, body { width: 1200px; height: 905px; overflow: hidden; }
  body {
    background: var(--stage);
    font-family: "Lato", Arial, sans-serif;
    position: relative;
  }
  .card {
    position: absolute;
    width: 600px;
    height: 340px;
    box-shadow: 0 10px 30px rgba(0,0,0,.45);
    overflow: hidden;
  }

  /* Back of card */
  .card-back { left: 110px; top: 80px; background: var(--card-black); }
  .back-mark {
    position: absolute; left: 190px; top: 20px;
    width: 300px; height: 300px;
    background: var(--silver-faint);
  }
  .back-brand {
    position: absolute; left: 70px; top: 130px;
    display: flex; align-items: center; gap: 16px;
    color: var(--silver);
  }
  .back-brand .brand-square { width: 44px; height: 44px; background: var(--silver); }
  .back-brand .brand-name { font-size: 46px; font-weight: 900; letter-spacing: 1px; }
  .back-tagline {
    position: absolute; right: 24px; bottom: 22px;
    color: var(--tagline); font-size: 14.5px; font-weight: 400;
  }

  /* Front of card */
  .card-front { left: 490px; top: 480px; background: var(--card-white); color: var(--ink); }
  .front-brand {
    position: absolute; left: 36px; top: 64px;
    display: flex; align-items: center; gap: 12px;
  }
  .front-brand .brand-square { width: 34px; height: 34px; background: var(--ink); }
  .front-brand .brand-name { font-size: 38px; font-weight: 900; letter-spacing: 1px; }
  .rule { position: absolute; height: 2px; background: var(--ink); }
  .rule-top { left: 270px; right: 36px; top: 138px; }
  .rule-left { left: 36px; width: 220px; top: 236px; }
  .corner-square {
    position: absolute; right: 40px; top: 154px;
    width: 74px; height: 74px; background: var(--ink);
  }
  .person { position: absolute; left: 36px; top: 174px; }
  .person-name { font-size: 20px; font-weight: 900; }
  .person-role { font-size: 16px; margin-top: 4px; }
  .contact-list { position: absolute; list-style: none; font-size: 17px; }
  .contact-list li { display: flex; align-items: center; gap: 8px; height: 30px; white-space: nowrap; }
  .contact-list svg { width: 14px; height: 14px; fill: var(--ink); flex: none; }
  .contact-online { left: 270px; top: 160px; }
  .contact-phone { left: 40px; top: 250px; }
</style>
</head>
<body>

<section class="card card-back" aria-label="Back of business card">
  <div class="back-mark" aria-hidden="true"></div>
  <div class="back-brand">
    <span class="brand-square"></span>
    <span class="brand-name">Kernwerk AG</span>
  </div>
  <p class="back-tagline">Reputation Management, Vextor &amp; Seo Services and Software development.</p>
</section>

<section class="card card-front" aria-label="Front of business card">
  <div class="front-brand">
    <span class="brand-square"></span>
    <span class="brand-name">Kernwerk AG</span>
  </div>
  <div class="rule rule-top"></div>
  <div class="corner-square" aria-hidden="true"></div>

  <div class="person">
    <p class="person-name">Jonas Weber</p>
    <p class="person-role">Director</p>
  </div>

  <ul class="contact-list contact-online">
    <li>
      <svg viewBox="0 0 16 16" aria-hidden="true"><path d="M0 3h16v10H0z M1 4l7 5 7-5v-0.1H1z" fill-rule="evenodd"/></svg>
      info@kernwerkag.com
    </li>
    <li>
      <svg viewBox="0 0 16 16" aria-hidden="true"><path d="M8 0a8 8 0 1 0 0 16A8 8 0 0 0 8 0zm-1 1.1C5.6 2.6 5 4.6 4.9 7.3H1.1A7 7 0 0 1 7 1.1zm2 0a7 7 0 0 1 5.9 6.2h-3.8C11 4.6 10.4 2.6 9 1.1zM7 2.2v5.1H6c.1-2.1.4-3.8 1-5.1zm2 0c.6 1.3.9 3 1 5.1H9zM1.1 8.7h3.8c.1 2.7.7 4.7 2.1 6.2A7 7 0 0 1 1.1 8.7zm4.9 0h1v5.1c-.6-1.3-.9-3-1-5.1zm3 0h1c-.1 2.1-.4 3.8-1 5.1zm2.1 0h3.8A7 7 0 0 1 9 14.9c1.4-1.5 2-3.5 2.1-6.2z"/></svg>
      www.kernwerkag.com
    </li>
  </ul>

  <div class="rule rule-left"></div>

  <ul class="contact-list contact-phone">
    <li>
      <svg viewBox="0 0 16 16" aria-hidden="true"><path d="M1 5c0-2 3-3 7-3s7 1 7 3v1h-4V4.5H5V6H1z M3 7h10l2 7H1z M8 9a2 2 0 1 0 0 4 2 2 0 0 0 0-4z"/></svg>
      040 555 0182
    </li>
    <li>
      <svg viewBox="0 0 16 16" aria-hidden="true"><path d="M4 0h8a1 1 0 0 1 1 1v14a1 1 0 0 1-1 1H4a1 1 0 0 1-1-1V1a1 1 0 0 1 1-1zm1 2v11h6V2z" fill-rule="evenodd"/></svg>
      079 5550 147
    </li>
  </ul>
</section>

</body>
</html>
```